Business Card Design

I am an Event and Wedding Planner in need of an eye catching business card featuring my logo (attached), my contact details, and my company tagline (Making every celebration glow with wonder...) I would like the tagline in font similar the logo's font.
Updates
I have just noticed that my logo has a misspelling so for the final design, I will be uploading a corrected logo as soon as I have it.
My apologies.
Reason: Waiting on a corrected logo...Lantern is misspelled and it should say Weddings not Wedding
The logo has been corrected so now Lantern is spelled correctly and it says Weddings instead of Wedding. Please use Edwardian Script ITC as the font for the tagline so it will match the logo. Thank you for your patience.
Target Market(s)
Engaged couples and people hosting milestone celebrations. 25-50 years old, predominately female
Industry/Entity Type
Business
Contact Information for Business Card
Rosalind Merrow, Event Manager / Owner, Mobile: 0491 868 254, Email: rosalind@velvetlanternco.com.au, www.velvetlanternco.com.au, Making every celebration glow with wonder...

```html
<!DOCTYPE html>
<html lang="en">
<head>
<meta charset="utf-8">
<title>Velvet Lantern – Business Card</title>
<link rel="stylesheet" href="https://fonts.googleapis.com/css2?family=EB+Garamond:wght@400;500&family=Great+Vibes&display=swap">
<style>
  :root {
    --backdrop: #2a2a2c;
    --card-white: #f7f7f7;
    --card-silver: #e6e6e6;
    --brand-red: #ec2227;
    --ink: #1c1c1c;
    --rule-grey: #6d6d6d;
    --paper: #ffffff;
  }
  * { margin: 0; padding: 0; box-sizing: border-box; }
  html, body {
    width: 1200px; height: 900px; overflow: hidden;
    background: var(--backdrop);
  }
  .canvas {
    position: relative; width: 1200px; height: 900px;
    display: flex; flex-direction: column; align-items: center; justify-content: center; gap: 30px;
  }
  .card {
    position: relative; width: 700px; height: 400px; overflow: hidden;
    box-shadow: 0 10px 28px rgba(0,0,0,.45);
  }

  /* Front */
  .card-front {
    background: radial-gradient(ellipse at 40% 30%, var(--card-white) 0%, var(--card-silver) 100%);
  }
  .front-brand {
    position: absolute; left: 48px; top: 58px;
    display: flex; align-items: center; gap: 14px;
  }
  .brand-name {
    font-family: "EB Garamond", serif; font-weight: 400;
    font-size: 46px; letter-spacing: 1px; color: var(--ink);
  }
  .brand-dot { width: 14px; height: 14px; border-radius: 50%; background: var(--brand-red); }
  .front-rule {
    position: absolute; left: 48px; top: 128px; width: 250px; height: 1px; background: var(--rule-grey);
  }
  .front-ornament {
    position: absolute; right: 20px; top: 30px; width: 300px; height: 170px;
    background: radial-gradient(ellipse at 60% 40%, rgba(236,34,39,.55) 0%, rgba(236,34,39,.15) 60%, rgba(236,34,39,0) 75%);
  }
  .front-line {
    position: absolute; left: 0; right: 0; top: 240px; height: 3px; background: var(--brand-red);
  }
  .front-email {
    position: absolute; right: 36px; top: 318px;
    font-family: "EB Garamond", serif; font-size: 20px; color: var(--ink);
  }

  /* Back */
  .card-back { display: flex; background: var(--paper); }
  .back-left { position: relative; width: 300px; height: 100%; background: var(--paper); }
  .tagline {
    position: absolute; left: 28px; top: 30px; width: 250px;
    font-family: "Great Vibes", cursive; font-size: 25px; line-height: 1.2; color: var(--brand-red);
  }
  .floral {
    position: absolute; left: 30px; bottom: 40px; width: 140px; height: 210px;
    background: linear-gradient(160deg, rgba(40,40,40,.08) 0%, rgba(40,40,40,.22) 55%, rgba(230,215,200,.5) 100%);
    border-radius: 8px;
  }
  .pattern-band {
    width: 26px; height: 100%;
    background: linear-gradient(90deg, rgba(236,34,39,.35), rgba(236,34,39,.75));
  }
  .back-right {
    position: relative; flex: 1; background: var(--brand-red); color: var(--paper);
    text-align: center; font-family: "EB Garamond", serif;
  }
  .back-brand {
    position: absolute; top: 52px; left: 0; right: 0;
    display: flex; justify-content: center; align-items: center; gap: 12px;
  }
  .back-brand .brand-name { color: var(--paper); font-size: 38px; }
  .back-brand .brand-dot { background: var(--paper); width: 12px; height: 12px; }
  .back-rule { position: absolute; top: 112px; left: 110px; right: 110px; height: 1px; background: rgba(255,255,255,.8); }
  .person-name { position: absolute; top: 148px; left: 0; right: 0; font-size: 36px; }
  .person-role { position: absolute; top: 196px; left: 0; right: 0; font-size: 17px; }
  .contact { position: absolute; top: 298px; left: 0; right: 0; font-size: 18px; line-height: 1.45; }
</style>
</head>
<body>
<main class="canvas">
  <section class="card card-front" aria-label="Card front">
    <div class="front-brand"><span class="brand-name">Velvet Lantern</span><span class="brand-dot"></span></div>
    <div class="front-rule"></div>
    <div class="front-ornament" role="img" aria-label="Red flourish ornament"></div>
    <div class="front-line"></div>
    <p class="front-email">rosalind@velvetlanternco.com.au</p>
  </section>

  <section class="card card-back" aria-label="Card back">
    <div class="back-left">
      <p class="tagline">Making every celebration glow with wonder...</p>
      <div class="floral" role="img" aria-label="Black line floral illustration"></div>
    </div>
    <div class="pattern-band" role="img" aria-label="Red lattice pattern band"></div>
    <div class="back-right">
      <div class="back-brand"><span class="brand-name">Velvet Lantern</span><span class="brand-dot"></span></div>
      <div class="back-rule"></div>
      <p class="person-name">Rosalind Merrow</p>
      <p class="person-role">Event Manager</p>
      <p class="contact">www.velvetlanternco.com.au<br>0491 868 254</p>
    </div>
  </section>
</main>
</body>
</html>
```